Wealth management Facebook Advertisement

Hello, we are trying to capture more leads to our online booking link through Facebook advertisement. We want an attractive modern design to get more clients and catch the attention of high net-worth clients. We deal with high-net-worth retirees, business owners, farmers, and wealth transfer. We offer high-net-worth client solutions that cover Financial Planning, Retirement and Estate Planning, Investment Planning, Tax Planning, and Insurance Planning. The final design that we would be looking for is modern and eye-catching and makes the prospective clients want to click our meeting link to schedule an introductory consultation.

We are in the Wealth Management / Financial Planning industry

Our online booking link Is the following :

https://calendar.brisquelmail.com/owa/calendar/MarcusFenleyPartnersRQPrivateWealth@tovrelfinancial.net/bookings/

Our current Facebook page is the following:

https://www.plorvenet.com/FenleyPrivateWealth

Please ask any further questions for needed information for creating design

```html
<!DOCTYPE html>
<html lang="en">
<head>
<meta charset="utf-8">
<title>Holistic Financial Plan – Facebook Ads</title>
<link rel="stylesheet" href="https://fonts.googleapis.com/css2?family=Oswald:wght@700&family=Montserrat:wght@300;600&family=Arimo:wght@400&display=swap">
<style>
  :root {
    --board: #2a2a2a;
    --navy: #0b2466;
    --bar: #04206a;
    --blue: #0a6fd0;
    --white: #ffffff;
    --photo-light: #f7f8fb;
    --photo-dark: #6c6a6a;
  }
  * { margin: 0; padding: 0; box-sizing: border-box; }
  html, body {
    width: 1200px; height: 1200px; overflow: hidden;
    background: var(--board);
  }
  .ad { position: absolute; overflow: hidden; background: var(--photo-light); }
  .ad--banner { left: 112px; top: 201px; width: 976px; height: 408px; }
  .ad--square { left: 384px; top: 650px; width: 432px; height: 432px; }

  .ad__photo { position: absolute; inset: 0; }
  .ad--banner .ad__photo {
    background:
      linear-gradient(90deg, var(--photo-light) 0%, rgba(247,248,251,.92) 30%, rgba(247,248,251,0) 62%),
      linear-gradient(160deg, #b9a58f 0%, #8e8a88 30%, #dfe3ea 55%, #eef1f6 70%, var(--photo-dark) 100%);
  }
  .ad--square .ad__photo {
    background:
      linear-gradient(0deg, rgba(247,248,251,.95) 0%, rgba(247,248,251,.6) 30%, rgba(247,248,251,0) 55%),
      linear-gradient(90deg, var(--photo-light) 0%, rgba(247,248,251,.7) 25%, rgba(247,248,251,0) 55%),
      linear-gradient(150deg, #d9c7ae 0%, #8c8580 35%, #cfd3da 60%, #eceff4 75%, var(--photo-dark) 100%);
  }

  .brand {
    position: absolute; display: flex; align-items: center;
    font-family: "Montserrat", sans-serif; font-weight: 600;
    color: var(--navy); text-transform: uppercase; line-height: 1.1;
  }
  .brand__mark { background: var(--navy); flex: none; }
  .brand__name span { display: block; }
  .ad--banner .brand { left: 90px; top: 62px; font-size: 12px; gap: 8px; }
  .ad--banner .brand__mark { width: 24px; height: 24px; }
  .ad--square .brand { left: 19px; top: 19px; font-size: 10px; gap: 7px; }
  .ad--square .brand__mark { width: 20px; height: 20px; }

  .headline { font-family: "Oswald", sans-serif; font-weight: 700; text-transform: uppercase; }
  .headline__lead, .headline__main { position: absolute; white-space: nowrap; line-height: 1; }
  .headline__lead { color: var(--navy); }
  .headline__main { color: var(--blue); }
  .ad--banner .headline__lead { left: 88px; top: 116px; font-size: 39.5px; letter-spacing: 0.7px; }
  .ad--banner .headline__main { left: 88px; top: 153px; font-size: 50.6px; letter-spacing: 2px; }
  .ad--square .headline__lead { left: 16px; top: 247px; font-size: 33.3px; letter-spacing: 1.1px; }
  .ad--square .headline__main { left: 16px; top: 278px; font-size: 44.4px; letter-spacing: 1.7px; }

  .rule { position: absolute; height: 1.5px; background: var(--navy); }
  .ad--banner .rule { left: 88px; top: 210px; width: 382px; }
  .ad--square .rule { left: 16px; top: 327px; width: 334px; }

  .tagline {
    position: absolute; font-family: "Montserrat", sans-serif; font-weight: 300;
    color: var(--navy); line-height: 1.08; white-space: nowrap;
  }
  .ad--banner .tagline { left: 88px; top: 215px; font-size: 19.5px; }
  .ad--square .tagline { left: 16px; top: 333px; font-size: 17px; }

  .cta {
    position: absolute; left: 0; background: var(--bar); color: var(--white);
    font-family: "Arimo", sans-serif; letter-spacing: 1.6px;
    display: flex; align-items: center; justify-content: flex-end;
    border-radius: 0 3px 3px 0; white-space: nowrap;
  }
  .ad--banner .cta { top: 279px; width: 397px; height: 35px; font-size: 15px; padding-right: 9px; }
  .ad--square .cta { top: 388px; width: 288px; height: 31px; font-size: 13px; padding-right: 8px; }
</style>
</head>
<body>

<section class="ad ad--banner">
  <div class="ad__photo" role="img" aria-label="Photo of an advisor's hand pointing a pen at financial charts and tables beside a calculator on a desk"></div>
  <div class="brand">
    <span class="brand__mark"></span>
    <div class="brand__name">
      <span>Marcus Fenley</span>
      <span>&amp; Partners</span>
    </div>
  </div>
  <h1 class="headline">
    <span class="headline__lead">Need a holistic</span>
    <span class="headline__main">Financial plan?</span>
  </h1>
  <div class="rule"></div>
  <p class="tagline">We create synchronized financial plans<br>designed for you and your family</p>
  <div class="cta">www.marcusfenleyandpartners.ca/</div>
</section>

<section class="ad ad--square">
  <div class="ad__photo" role="img" aria-label="Photo of an advisor's hand pointing a pen at financial charts and tables beside a calculator on a desk"></div>
  <div class="brand">
    <span class="brand__mark"></span>
    <div class="brand__name">
      <span>Marcus Fenley</span>
      <span>&amp; Partners</span>
    </div>
  </div>
  <h2 class="headline">
    <span class="headline__lead">Need a holistic</span>
    <span class="headline__main">Financial plan?</span>
  </h2>
  <div class="rule"></div>
  <p class="tagline">We create synchronized financial plans<br>designed for you and your family</p>
  <div class="cta">www.marcusfenleyandpartners.ca/</div>
</section>

</body>
</html>
```